Investment company needing business card

We are wanting a business card which looks sharp and easy on the eye. We are thinking of having a business card with the logo embossed on it, to really make it stand out. We will only have a small amount of information of the business card, person's name, position, email address and phone number

Contact Information for Business Card

Danielle Frost
Executive Assistant
+64 21 473 5162
danielf@harwickpartners.co.nz

Requirements
Must have
• Embossed logo
Should not have
• Not to be busy

```html
<!DOCTYPE html>
<html lang="en">
<head>
<meta charset="utf-8">
<title>Harwick Partners – Business Card</title>
<link href="https://fonts.googleapis.com/css2?family=Open+Sans:wght@400;600;700&display=swap" rel="stylesheet">
<style>
  :root {
    --backdrop: #e4e1dd;
    --card: #fbfbfb;
    --green: #1fa86a;
    --charcoal: #5f6062;
    --ink: #3b3f47;
    --muted: #6b6d70;
    --rule: #c9c9c9;
  }
  * { margin: 0; padding: 0; box-sizing: border-box; }
  html, body {
    width: 1200px; height: 997px; overflow: hidden;
    background: var(--backdrop);
    font-family: "Open Sans", Arial, sans-serif;
  }
  .stage {
    position: relative; width: 1200px; height: 997px;
    display: flex; align-items: center; justify-content: center; gap: 60px;
  }
  .card {
    position: relative; width: 520px; height: 297px;
    background: var(--card);
    box-shadow: 0 2px 6px rgba(0,0,0,0.12);
  }
  .brand {
    position: absolute; display: flex; align-items: center; gap: 10px;
  }
  .brand-mark { width: 30px; height: 30px; background: var(--green); }
  .brand-name {
    font-weight: 700; color: var(--green); font-size: 19px; letter-spacing: 1.5px;
  }
  .card-front .brand { left: 34px; top: 40px; }
  .holder {
    position: absolute; right: 34px; top: 98px; text-align: right;
  }
  .holder-name {
    font-size: 15px; font-weight: 600; color: var(--ink); letter-spacing: 0.3px;
    padding-bottom: 4px; border-bottom: 2px solid var(--green);
    display: inline-block; min-width: 150px;
  }
  .holder-role { font-size: 11px; color: var(--muted); margin-top: 4px; }
  .website {
    position: absolute; right: 34px; top: 152px; font-size: 11px; color: var(--muted);
  }
  .band {
    position: absolute; left: 0; right: 0; top: 172px; height: 7px;
    background: var(--charcoal);
  }
  .band-accent {
    position: absolute; right: 0; top: 0; width: 125px; height: 7px; background: var(--green);
  }
  .band-rule {
    position: absolute; left: 34px; right: 0; top: 186px; height: 1px; background: var(--rule);
  }
  .contacts {
    position: absolute; left: 34px; bottom: 30px; list-style: none;
    font-size: 11px; color: var(--muted);
  }
  .contacts li { display: flex; align-items: center; gap: 7px; margin-top: 4px; }
  .contacts svg { width: 10px; height: 10px; fill: var(--green); }
  .card-back { display: flex; align-items: center; justify-content: center; }
  .card-back .brand { position: static; gap: 14px; }
  .card-back .brand-mark { width: 40px; height: 40px; }
  .card-back .brand-name { font-size: 26px; letter-spacing: 2px; }
</style>
</head>
<body>
<main class="stage">
  <section class="card card-front">
    <div class="brand">
      <span class="brand-mark"></span>
      <span class="brand-name">HARWICK PARTNERS</span>
    </div>
    <div class="holder">
      <p class="holder-name">DANIELLE FROST</p>
      <p class="holder-role">Executive Assistant</p>
    </div>
    <p class="website">www.harwickpartners.co.nz</p>
    <div class="band"><span class="band-accent"></span></div>
    <div class="band-rule"></div>
    <ul class="contacts">
      <li>
        <svg viewBox="0 0 10 10" aria-hidden="true"><rect x="2.5" y="0" width="5" height="10" rx="1"/><rect x="3.5" y="1.5" width="3" height="5" fill="#fbfbfb"/></svg>
        +64 21 473 5162
      </li>
      <li>
        <svg viewBox="0 0 10 10" aria-hidden="true"><rect x="0" y="2" width="10" height="6.5" rx="1"/><path d="M0.5 2.5 L5 6 L9.5 2.5" stroke="#fbfbfb" stroke-width="1" fill="none"/></svg>
        danielf@harwickpartners.co.nz
      </li>
    </ul>
  </section>
  <section class="card card-back">
    <div class="brand">
      <span class="brand-mark"></span>
      <span class="brand-name">HARWICK PARTNERS</span>
    </div>
  </section>
</main>
</body>
</html>
```